Business Card Design

We are a manufacturing and distribution company with most of our customer base being supermarkets. We have established brand guidelines that are attached.

```html
<!DOCTYPE html>
<html lang="en">
<head>
<meta charset="utf-8">
<title>Corvalle Business Card</title>
<link href="https://fonts.googleapis.com/css2?family=Montserrat:wght@400;500;700;800&display=swap" rel="stylesheet">
<style>
  :root {
    --backdrop: #6e6e6e;
    --paper: #ffffff;
    --ink: #111111;
    --muted: #6b6b6b;
    --brand-blue: #0a5fc2;
    --brand-blue-light: #1aa9e8;
    --brand-blue-deep: #0a4f9e;
    --brand-red: #ee2a1e;
    --brand-red-light: #f6553e;
  }
  * { margin: 0; padding: 0; box-sizing: border-box; }
  html, body {
    width: 1200px;
    height: 1056px;
    overflow: hidden;
    background: var(--backdrop);
    font-family: "Montserrat", Arial, sans-serif;
  }
  .canvas {
    position: relative;
    width: 1200px;
    height: 1056px;
  }
  .card {
    position: absolute;
    left: 250px;
    width: 700px;
    height: 400px;
    overflow: hidden;
    box-shadow: 0 14px 30px rgba(0,0,0,0.28);
  }
  /* Front */
  .card-front {
    top: 96px;
    background: var(--paper);
  }
  .brand-name {
    position: absolute;
    left: 70px;
    top: 170px;
    font-weight: 800;
    font-size: 40px;
    letter-spacing: 2px;
    color: var(--ink);
  }
  .accent-rule {
    position: absolute;
    top: 308px;
    height: 5px;
    border-radius: 3px;
  }
  .accent-rule.red {
    left: 60px;
    width: 300px;
    background: linear-gradient(90deg, var(--brand-red), var(--brand-red-light), var(--brand-red));
  }
  .accent-rule.blue {
    left: 366px;
    width: 276px;
    background: linear-gradient(90deg, var(--brand-blue), var(--brand-blue-light), var(--brand-blue));
  }
  .person {
    position: absolute;
    left: 405px;
    top: 120px;
  }
  .person-name {
    font-size: 27px;
    color: var(--brand-blue);
    font-weight: 500;
    letter-spacing: 1px;
    line-height: 1;
  }
  .person-name .first { font-weight: 800; }
  .person-role {
    font-size: 14px;
    color: var(--muted);
    margin-top: 4px;
  }
  .contacts {
    list-style: none;
    margin-top: 22px;
  }
  .contacts li {
    display: flex;
    align-items: center;
    gap: 10px;
    font-size: 13.5px;
    color: #3a3a3a;
    height: 30px;
  }
  .contacts svg { flex: 0 0 18px; }
  /* Back */
  .card-back {
    top: 560px;
    background: linear-gradient(125deg, var(--brand-blue) 0%, var(--brand-blue-light) 48%, var(--brand-blue-deep) 100%);
  }
  .back-name {
    position: absolute;
    right: 56px;
    bottom: 62px;
    font-weight: 800;
    font-size: 36px;
    letter-spacing: 2px;
    color: var(--paper);
  }
</style>
</head>
<body>
<main class="canvas">
  <section class="card card-front" aria-label="Business card front">
    <div class="brand-name">CORVALLE</div>
    <div class="accent-rule red"></div>
    <div class="accent-rule blue"></div>
    <div class="person">
      <div class="person-name"><span class="first">DARA</span> WELLS</div>
      <div class="person-role">Manager</div>
      <ul class="contacts">
        <li>
          <svg width="18" height="18" viewBox="0 0 18 18" aria-hidden="true">
            <rect width="18" height="18" rx="3" fill="#ee2a1e"/>
            <path d="M5.5 4.2c.5-.4 1.1-.3 1.4.2l.9 1.5c.3.5.1 1-.3 1.3l-.6.4c.5 1.2 1.4 2.1 2.6 2.6l.4-.6c.3-.4.9-.6 1.3-.3l1.5.9c.5.3.6.9.2 1.4l-.7.8c-.5.5-1.2.6-1.9.3C7.9 11.8 6.2 10.1 5.3 7.7c-.3-.7-.2-1.4.3-1.9z" fill="#fff"/>
          </svg>
          (555) 014-2870
        </li>
        <li>
          <svg width="18" height="18" viewBox="0 0 18 18" aria-hidden="true">
            <rect width="18" height="18" rx="3" fill="#ee2a1e"/>
            <rect x="4" y="5.5" width="10" height="7" fill="none" stroke="#fff" stroke-width="1.2"/>
            <path d="M4 5.5l5 4 5-4M4 12.5l3.6-3.4M14 12.5l-3.6-3.4" fill="none" stroke="#fff" stroke-width="1.1"/>
          </svg>
          info@corvallemail.com
        </li>
        <li>
          <svg width="18" height="18" viewBox="0 0 18 18" aria-hidden="true">
            <rect width="18" height="18" rx="3" fill="#ee2a1e"/>
            <path d="M6 4.5l6.5 5.2-3 .4 1.7 3.1-1.2.6-1.7-3.1-2.2 2z" fill="#fff"/>
          </svg>
          www.corvalle.com
        </li>
      </ul>
    </div>
  </section>

  <section class="card card-back" aria-label="Business card back">
    <div class="back-name">CORVALLE</div>
  </section>
</main>
</body>
</html>
```